Layout für Broschüre für chemiefreie Lösung, Kühlwasser aufzubereiten
Zielgruppe
FLUVITEK hat eine Technologie entwickelt, die in der Industrie eingesetzt wird um in geschlossenen und offenen Kühlkreisläufen ohne Biozide und Korrosion Inhibitoren das Kühlwasser aufzubereiten. Mit FLUVITEK haben die Unternehmen eine chemiefreie Lösungen gegen Biofouling, Korrosion und Kalk. Zielgruppe sind alle Unternehmen die etwas produzieren oder Klimaanlagen / Heizungssysteme betreiben. Es geht um zukunftsorientierte und vor allem nachhaltige Technologie ohne Einsatz von Chemie.
Aufgabenstellung
Wir suchen für die Broschüre ein neues Layout, dass geradlinig und klar strukturiert ist, vor allem modern. Die Broschüre sollte DIN A 4 - Format sein in der gewohnten Struktur Umschlagseite innen und außen und 8 - 10 Innenseiten. Im Layout sollte ein roter Faden zu erkennen sein, aber nicht jede Seite gleich aussehen. Die Anlagen sind nur beispielhaft vom bestehenden Material und sollten vom Layout keinesfalls eine Orientierung geben, denn das soll verändert werden. Die Anlagen sind für einen inhaltlichen Überblick.

```html
<!DOCTYPE html>
<html lang="de">
<head>
<meta charset="utf-8">
<title>Wirkungsweise – Broschüre Doppelseite</title>
<link href="https://fonts.googleapis.com/css2?family=Lato:wght@300;400;700&family=Arimo:wght@400&display=swap" rel="stylesheet">
<style>
  :root {
    --backdrop: #dcdcdc;
    --paper: #f7f7f5;
    --teal-dark: #0b4750;
    --teal-mid: #1d6f7a;
    --teal-soft: #3f8b93;
    --cyan: #2aa9c6;
    --ink: #1a1a1a;
    --ink-soft: #3a3a3a;
    --muted-light: #8fb4b8;
    --rule: #b9b9b9;
  }
  * { box-sizing: border-box; margin: 0; padding: 0; }
  html, body {
    width: 1200px; height: 900px; overflow: hidden;
    background: var(--backdrop);
    font-family: "Lato", sans-serif;
  }
  .spread {
    position: absolute; left: 160px; top: 100px;
    width: 880px; height: 700px;
    display: flex;
  }
  .page {
    position: relative; width: 440px; height: 700px;
    background: var(--paper);
  }
  .page--left { border-right: 1px solid #e2e2e0; }

  /* left page */
  .section-title {
    position: absolute; left: 84px; top: 114px; width: 269px; height: 57px;
    border: 2px solid var(--teal-dark);
    display: flex; align-items: center; justify-content: center;
    font-weight: 400; font-size: 19px; letter-spacing: 2.5px;
    color: var(--cyan);
  }
  .lead {
    position: absolute; left: 20px; right: 20px; top: 248px;
    text-align: center; text-transform: uppercase;
    font-family: "Arimo", sans-serif; font-size: 11px; line-height: 19px;
    letter-spacing: .8px; color: var(--ink);
  }
  .steps-band {
    position: absolute; left: 0; right: 0; top: 303px; height: 298px;
    background: linear-gradient(90deg, var(--teal-dark) 0%, var(--teal-dark) 45%, var(--teal-soft) 75%, var(--teal-mid) 100%);
    display: flex; justify-content: space-between; padding: 0 17px;
  }
  .step { width: 145px; text-align: center; }
  .step__icon { margin: 56px auto 0; display: block; }
  .step__label {
    margin-top: 34px; font-weight: 700; font-size: 11px; letter-spacing: 1px;
    color: var(--cyan);
  }
  .step__sub {
    margin-top: 6px; font-size: 9px; letter-spacing: .6px;
    text-transform: uppercase; color: #b8d0d3;
  }
  .step__text {
    margin-top: 14px; font-size: 8px; line-height: 11.5px; font-weight: 300;
    color: var(--muted-light); padding: 0 4px;
  }
  .folio {
    position: absolute; bottom: 24px; left: 30px; right: 30px;
    border-top: 1px solid var(--rule); padding-top: 5px;
    font-size: 7px; color: var(--ink-soft);
  }
  .folio--right { text-align: right; }

  /* right page */
  .headline {
    position: absolute; left: 65px; top: 50px;
    font-size: 19px; letter-spacing: 2.5px; font-weight: 400; color: var(--cyan);
  }
  .headline-rule {
    position: absolute; left: 65px; top: 76px; width: 253px; height: 3px;
    background: linear-gradient(90deg, var(--teal-mid), var(--teal-dark));
  }
  .body-copy {
    position: absolute; left: 66px; top: 112px; width: 328px;
    font-family: "Arimo", sans-serif; font-size: 10.5px; line-height: 13.6px;
    color: var(--ink);
  }
  .figure {
    position: absolute; left: 67px; top: 231px; width: 334px; height: 321px;
    border: 2px solid var(--teal-mid);
    background:
      radial-gradient(ellipse 70% 30% at 55% 25%, #2e9fc4 0%, #13506a 45%, transparent 75%),
      linear-gradient(180deg, #0e3c52 0%, #0b2a36 35%, #0c1413 50%, #0a0d0d 100%);
  }
  .figure__caption {
    position: absolute; left: 148px; top: 539px; width: 151px; height: 30px;
    background: var(--teal-soft);
    display: flex; align-items: center; justify-content: center;
    font-size: 10px; letter-spacing: 1.5px; color: #d9ecee;
  }
</style>
</head>
<body>
<main class="spread">
  <section class="page page--left">
    <h1 class="section-title">WIRKUNGSWEISE</h1>
    <p class="lead">Gent pediscitate peliquo destiam, quissus aut atur? Qui<br>aut officil maximaion eum ullupta turi</p>

    <div class="steps-band">
      <div class="step">
        <svg class="step__icon" width="76" height="76" viewBox="0 0 76 76" aria-hidden="true"><circle cx="38" cy="38" r="37" fill="#8a8a8a" stroke="#9a9a9a"/></svg>
        <h2 class="step__label">SCHRITT 1</h2>
        <p class="step__sub">Inis enturit dolupta</p>
        <p class="step__text">Calcium(+) und Bicarbonat(-) liegen gebunden im Wasser vor. Weiterhin Salze, Chloride, Sulfate, Metallionen, Mikrobiologie</p>
      </div>
      <div class="step">
        <svg class="step__icon" width="76" height="76" viewBox="0 0 76 76" aria-hidden="true"><circle cx="38" cy="38" r="37" fill="#939393" stroke="#a3a3a3"/></svg>
        <h2 class="step__label">SCHRITT 2</h2>
        <p class="step__sub">Explique coreniendi</p>
        <p class="step__text">Energieeintrag über Frequenz-Impulstechnologie</p>
      </div>
      <div class="step">
        <svg class="step__icon" width="76" height="76" viewBox="0 0 76 76" aria-hidden="true"><circle cx="38" cy="38" r="37" fill="#aeaeae" stroke="#bdbdbd"/></svg>
        <h2 class="step__label">SCHRITT 3</h2>
        <p class="step__sub">Ga. Bit laborest, se-</p>
        <p class="step__text">Alle +/- geladenen Teilchen geraten in Schwingung (Wassermoleküle als Dipole). Gelöste Ionen reagieren miteinander</p>
      </div>
    </div>

    <footer class="folio">4 Chemiefreie</footer>
  </section>

  <section class="page page--right">
    <h2 class="headline">ÜBERSCHRIFT</h2>
    <div class="headline-rule"></div>
    <p class="body-copy">Lorem ipsum dolor sit amet, consetetur sadipscing elitr, sed diam nonumy eirmod tempor invidunt ut labore et dolore magna aliquyam erat, sed diam voluptua. At vero eos et accusam et justo duo dolores et ea rebum. Stet clita kasd gubergren, no sea takimata sanctus est Lorem ipsum dolor sit amet.</p>
    <div class="figure" role="img" aria-label="Foto: Wassertropfen, der aus einer blau beleuchteten Wasseroberfläche vor dunklem Hintergrund fällt"></div>
    <div class="figure__caption">BILDTITEL</div>
    <footer class="folio folio--right">Chemiefreie 5</footer>
  </section>
</main>
</body>
</html>
```